Design and Renovation Company Luxury Business Card

I want to create a luxury business card for a Design and Renovation Firm . We will use our current logo. The company name is 528BUILDA. We do not want anything standard. We need a very unique concept.
Please see uploaded inspiration. I really like the textured paper option. I would like the card to be thick with debossing, and/or embossing options. The logo has orange in it but I would like to see the card with and without the orange. I think the orange may make the company feel less high-end. The goal is to elevate the logo not match its vibe per se of the logo. We want something very unique, not standard at all!
I would like a space for :
Logo,
Name,
Position,
Email,
Office number,
Website Address,
Business Address,
Thank you!
Have fun!
Target Market(s)
Home owners Age 35 +
Industry/Entity Type
Design and Renovation
Contact Information for Business Card
Logo, Name, Position, Email, Office number, Website Address, Business Address,.
Colors
Designer to choose colors to be used in the design.
Requirements
Must have
- A luxury designer feel. Must be black or dark grey but open to other luxury ideas.
Nice to have
- Gold, silver, black embossing or debossing. Textured paper design.
Should not have
- A cheap look and feel.

```html
<!DOCTYPE html>
<html lang="en">
<head>
<meta charset="utf-8">
<title>528BUILDA Business Card</title>
<link href="https://fonts.googleapis.com/css2?family=Lato:wght@400;700&family=Montserrat:wght@500;700&display=swap" rel="stylesheet">
<style>
  :root {
    --backdrop: #e0e0e0;
    --card: #1c1c1d;
    --card-back: #1e1e1f;
    --accent: #e62228;
    --ink: #ffffff;
    --rule: #3a3a3b;
  }
  html, body {
    margin: 0;
    padding: 0;
    width: 1200px;
    height: 1000px;
    overflow: hidden;
    background: var(--backdrop);
  }
  .canvas {
    position: relative;
    width: 1200px;
    height: 1000px;
  }
  .card {
    position: absolute;
    left: 203px;
    width: 794px;
    height: 454px;
    border-radius: 22px;
    overflow: hidden;
  }
  .card--front {
    top: 40px;
    background: var(--card);
  }
  .card--back {
    top: 506px;
    background: var(--card-back);
  }

  /* Front: company name */
  .wordmark {
    position: absolute;
    left: 0;
    right: 0;
    top: 202px;
    text-align: center;
    font-family: "Lato", sans-serif;
    font-weight: 700;
    font-size: 44px;
    letter-spacing: 6px;
    color: var(--ink);
    line-height: 1;
  }

  /* Back: small company name */
  .wordmark-mini {
    position: absolute;
    right: 28px;
    top: 108px;
    font-family: "Lato", sans-serif;
    font-weight: 700;
    font-size: 15px;
    letter-spacing: 1.5px;
    color: var(--ink);
  }

  /* Back: identity */
  .identity {
    position: absolute;
    right: 448px;
    top: 190px;
    text-align: right;
  }
  .identity__name {
    font-family: "Montserrat", sans-serif;
    font-weight: 700;
    font-size: 35px;
    color: var(--accent);
    margin: 0;
    line-height: 1;
  }
  .identity__role {
    font-family: "Montserrat", sans-serif;
    font-weight: 500;
    font-size: 17px;
    color: var(--ink);
    margin-top: 10px;
  }
  .divider {
    position: absolute;
    left: 383px;
    top: 124px;
    width: 1px;
    height: 190px;
    background: var(--rule);
  }

  /* Back: contact list */
  .contacts {
    position: absolute;
    left: 415px;
    top: 163px;
    margin: 0;
    padding: 0;
    list-style: none;
  }
  .contacts__item {
    display: flex;
    align-items: center;
    gap: 12px;
    height: 35px;
    font-family: "Lato", sans-serif;
    font-size: 21px;
    color: var(--ink);
    letter-spacing: 0.3px;
  }
  .contacts__icon {
    width: 26px;
    height: 26px;
    flex: none;
  }

  .address {
    position: absolute;
    left: 29px;
    top: 406px;
    display: flex;
    align-items: center;
    gap: 5px;
    font-family: "Lato", sans-serif;
    font-size: 18px;
    color: var(--ink);
  }
  .address__icon {
    width: 14px;
    height: 18px;
  }

  .sign-off {
    position: absolute;
    left: 460px;
    top: 348px;
    width: 284px;
    height: 86px;
    border-radius: 6px;
    background: linear-gradient(90deg, rgba(255,255,255,0.05), rgba(255,255,255,0.12));
  }
</style>
</head>
<body>
<main class="canvas">

  <section class="card card--front" aria-label="Card front">
    <div class="wordmark">528BUILDA</div>
  </section>

  <section class="card card--back" aria-label="Card back">
    <div class="wordmark-mini">528BUILDA</div>

    <div class="identity">
      <h1 class="identity__name">CLAIRE MORGAN</h1>
      <div class="identity__role">Managing Director</div>
    </div>

    <div class="divider"></div>

    <ul class="contacts">
      <li class="contacts__item">
        <svg class="contacts__icon" viewBox="0 0 26 26" aria-hidden="true">
          <rect x="1.5" y="1.5" width="23" height="23" rx="5" fill="none" stroke="var(--accent)" stroke-width="2"/>
          <path d="M8.5 7.5 l2.5 -0.5 1.3 3 -1.5 1.2 c0.8 1.7 2 2.9 3.6 3.6 l1.2 -1.5 3 1.3 -0.5 2.5 c-5.5 0.5 -10.1 -4.1 -9.6 -9.6z" fill="none" stroke="var(--accent)" stroke-width="1.5" stroke-linejoin="round"/>
        </svg>
        <span>061-482 730 195</span>
      </li>
      <li class="contacts__item">
        <svg class="contacts__icon" viewBox="0 0 26 26" aria-hidden="true">
          <rect x="1.5" y="1.5" width="23" height="23" rx="5" fill="none" stroke="var(--accent)" stroke-width="2"/>
          <path d="M6.5 13 L19 7.5 L15.5 19 L12.5 14.5 Z M12.5 14.5 L19 7.5" fill="none" stroke="var(--accent)" stroke-width="1.5" stroke-linejoin="round"/>
        </svg>
        <span>hello@528builda.com</span>
      </li>
      <li class="contacts__item">
        <svg class="contacts__icon" viewBox="0 0 26 26" aria-hidden="true">
          <rect x="1.5" y="1.5" width="23" height="23" rx="5" fill="none" stroke="var(--accent)" stroke-width="2"/>
          <circle cx="13" cy="13" r="6.5" fill="none" stroke="var(--accent)" stroke-width="1.5"/>
          <ellipse cx="13" cy="13" rx="2.8" ry="6.5" fill="none" stroke="var(--accent)" stroke-width="1.2"/>
          <line x1="6.5" y1="13" x2="19.5" y2="13" stroke="var(--accent)" stroke-width="1.2"/>
        </svg>
        <span>www.528builda.com</span>
      </li>
    </ul>

    <div class="address">
      <svg class="address__icon" viewBox="0 0 14 18" aria-hidden="true">
        <path d="M7 0.5 C3.4 0.5 0.8 3.1 0.8 6.6 C0.8 11 7 17.5 7 17.5 C7 17.5 13.2 11 13.2 6.6 C13.2 3.1 10.6 0.5 7 0.5Z" fill="var(--ink)"/>
        <circle cx="7" cy="6.5" r="2.3" fill="var(--card-back)"/>
      </svg>
      <span>4716 Harbor Ridge Blvd, 204-C, FL 32407</span>
    </div>

    <div class="sign-off" role="img" aria-label="Hand-lettered sign-off: Thank you, have fun"></div>
  </section>

</main>
</body>
</html>
```